Psychiatric Office Needs a Website- 1st Time Ever!

Been in practice since 2003 with no website, but finally ready to dive in. We are Maplecrest Behavioral Healthcare, a mental health outpatient practice based in Fayetteville, Georgia that sees diverse individuals and families from childhood to advanced age for a variety of conditions. We've grown by word of mouth and referral but would now like to have a digital footprint. Be the pioneer of our website and we will be sure to share. We would like to see designs that are modern, animated, fairly colorful, easy to read, and caters to all ages. Also, we would like the design to take the whole page (not be centered) and can be viewed well on phone/tablet. Please see our outline for more information. Our motto/slogan is: Maplecrest Behavioral Healthcare- A step forward in your wellness journey, so the design should try to reflect that.
Updates

Project Deadline Extended
Reason: site in progress

Target Market(s)

Children through elderly

Industry/Entity Type

Medical

Logo Text

Stepping forward in your wellness journey

Number of Pages Required

1 page

Colors

Designer to choose colors to be used in the design.

Requirements
Must have
• Animation or moving pictures.
• Color.
• Concise.
• User friendly
• Diversity in the stock photos

```html
<!DOCTYPE html>
<html lang="en">
<head>
<meta charset="utf-8">
<title>Maplecrest Behavioral Healthcare</title>
<link href="https://fonts.googleapis.com/css2?family=Raleway:wght@400;500;600;700&family=Open+Sans:wght@400;600&display=swap" rel="stylesheet">
<style>
:root{
  --green:#8dc63f;
  --green-dark:#7ab32e;
  --blue:#4fc3e8;
  --ink:#444;
  --ink-soft:#666;
  --muted:#888;
  --light-bg:#f3f3f3;
  --news-bg:#f5f6f8;
  --footer:#3b3b3b;
  --line:#dcdcdc;
  --white:#fff;
}
*{margin:0;padding:0;box-sizing:border-box}
html,body{width:1200px;height:2899px;overflow:hidden}
body{position:relative;font-family:"Open Sans",sans-serif;color:var(--ink);background:var(--white)}
.abs{position:absolute}
.heading{font-family:"Raleway",sans-serif}

/* top bar */
.topbar{position:absolute;left:0;top:0;width:1200px;height:48px;background:var(--green);color:var(--white);font-size:13px;font-weight:600}
.topbar .hours{position:absolute;left:87px;top:16px}
.topbar .phone{position:absolute;right:238px;top:16px}
.topbar .portal{position:absolute;left:981px;top:7px;width:132px;height:33px;border:1px solid var(--white);text-align:center;line-height:31px;font-size:12px}

/* header */
.header{position:absolute;left:0;top:48px;width:1200px;height:101px;background:var(--white)}
.brand{position:absolute;left:87px;top:14px}
.brand-mark{position:absolute;left:0;top:4px;width:56px;height:56px;border-radius:50%;background:var(--green)}
.brand-name{position:absolute;left:66px;top:10px;width:260px;font-family:"Raleway",sans-serif;font-weight:700;font-size:17px;line-height:21px;color:#2a6a8a}
.brand-tag{position:absolute;left:0;top:68px;white-space:nowrap;font-size:10px;color:#2a6a8a;font-weight:600}
.nav{position:absolute;right:87px;top:43px;display:flex;gap:34px;font-family:"Raleway",sans-serif;font-size:13px;font-weight:600;color:#333}
.nav .active{color:var(--green)}

/* hero */
.hero{position:absolute;left:0;top:149px;width:1200px;height:500px;background:linear-gradient(100deg,#e7e9ea 0%,#d6d9db 45%,#c4c8cb 70%,#dfe2e4 100%)}
.hero-panel{position:absolute;left:87px;top:147px;width:493px;height:264px;background:rgba(80,80,80,.55);padding:30px 20px}
.hero-panel .kicker{color:var(--white);font-family:"Raleway",sans-serif;font-size:22px;font-weight:500}
.hero-panel .slogan{margin-top:14px;color:var(--green);font-family:"Raleway",sans-serif;font-weight:700;font-size:30px;line-height:42px}
.btn-outline{position:absolute;left:22px;top:171px;width:194px;height:50px;border:1px solid var(--white);color:var(--white);font-family:"Raleway",sans-serif;font-size:15px;font-weight:600;text-align:center;line-height:48px}
.dots{position:absolute;left:87px;top:470px;display:flex;gap:10px}
.dots span{width:15px;height:15px;border-radius:50%;border:2px solid var(--white)}
.dots span.on{background:var(--white)}

/* welcome */
.welcome-title{left:87px;top:678px;font-size:30px;font-weight:400;color:#444}
.welcome-sub{left:87px;top:720px;font-size:22px;font-weight:700;color:var(--green)}
.body-text{font-size:12px;line-height:25px;color:var(--ink-soft)}
.btn-green{background:var(--green);color:var(--white);font-family:"Raleway",sans-serif;font-weight:600;font-size:15px;text-align:center}
.vision-title{left:713px;top:677px;font-size:23px;font-weight:600;color:#555}
.photo{position:absolute}
.link-more{left:713px;top:1040px;font-family:"Raleway",sans-serif;font-weight:700;font-size:14px;color:var(--green);text-decoration:underline}

/* services */
.services{position:absolute;left:0;top:1097px;width:1200px;height:536px;background:var(--light-bg)}
.section-title{position:absolute;left:0;width:1200px;text-align:center;font-family:"Raleway",sans-serif;font-weight:700;font-size:24px;color:#666}
.section-sub{position:absolute;left:0;width:1200px;text-align:center;font-size:11px;color:var(--muted)}

/* prospective / faq */
.prosp-title{left:87px;top:1668px;font-size:24px;font-weight:700;color:#555}
.faq-title{left:556px;top:1668px;font-size:24px;font-weight:700;color:#555}
.checklist{position:absolute;left:87px;top:1731px;list-style:none;font-size:13px;color:var(--ink-soft)}
.checklist li{height:40.4px;display:flex;align-items:center}
.checklist svg{margin-right:28px}
.faq-item{position:absolute;left:556px;width:557px;height:49px;border:1px solid var(--line);background:var(--white);font-size:13.5px;color:#555;padding:0 16px;line-height:47px}
.faq-item svg{position:absolute;right:16px;top:17px}
.faq-answer{left:572px;top:1790px;width:530px;font-size:11.5px;line-height:24px;color:var(--ink-soft)}

/* news */
.news{position:absolute;left:0;top:2035px;width:1200px;height:550px;background:var(--news-bg)}
.card{position:absolute;top:121px;width:326px}
.card .pic{width:326px;height:205px}
.card h3{margin-top:35px;font-family:"Raleway",sans-serif;font-weight:700;font-size:15px;color:#444}
.card .meta{margin-top:20px;padding-bottom:10px;border-bottom:1px solid var(--line);display:flex;justify-content:space-between;font-size:9px;color:var(--muted)}
.card p{margin-top:14px;font-size:11.5px;line-height:24px;color:var(--ink-soft)}

/* footer */
.footer{position:absolute;left:0;top:2585px;width:1200px;height:314px;background:var(--footer);color:#e6e6e6}
.footer h4{position:absolute;top:50px;font-family:"Raleway",sans-serif;font-weight:700;font-size:17px;color:var(--white)}
.foot-brand{position:absolute;left:97px;top:102px}
.foot-brand .brand-mark{top:0;width:54px;height:54px}
.foot-brand .brand-name{top:6px;left:66px;color:var(--white)}
.contact-list{position:absolute;left:410px;top:96px;list-style:none;font-size:12px;line-height:16px}
.contact-list li{display:flex;gap:14px;margin-bottom:13px}
.news-text{position:absolute;left:670px;top:95px;width:220px;font-size:12px;line-height:21px}
.email-input{position:absolute;left:670px;top:148px;width:204px;height:34px;background:var(--white);color:#999;font-size:11px;line-height:34px;padding-left:14px}
.subscribe{position:absolute;left:672px;top:190px;width:80px;height:27px;line-height:27px;font-size:10px}
.quick{position:absolute;left:950px;top:96px;list-style:none;font-size:11.5px}
.quick li{height:23.5px;display:flex;align-items:center;gap:14px}
.foot-rule{position:absolute;left:87px;top:251px;width:1026px;height:1px;background:#555}
.copyright{position:absolute;left:87px;top:275px;font-size:12px}
.social{position:absolute;left:1077px;top:267px;width:34px;height:34px;border-radius:50%;border:2px solid #ddd}
</style>
</head>
<body>

<!-- top bar -->
<div class="topbar">
  <div class="hours">&#9719;&nbsp; HOURS &nbsp;: MON - SAT : 08.00 am to 10.00 pm</div>
  <div class="phone">&#9742;&nbsp; PHONE : (770)-555-0142</div>
  <div class="portal">PATIENT PORTAL</div>
</div>

<!-- header -->
<header class="header">
  <div class="brand">
    <span class="brand-mark"></span>
    <div class="brand-name">Maplecrest Behavioral Healthcare</div>
    <div class="brand-tag">A STEP FORWARD IN YOUR WELLNESS JOURNEY</div>
  </div>
  <nav class="nav">
    <span class="active">HOME</span><span>ABOUT US</span><span>SERVICES</span><span>CONDITIONS WE TREAT</span><span>NEW PATIENTS</span><span>CONTACT US</span>
  </nav>
</header>

<!-- hero -->
<section class="hero" role="img" aria-label="Photo of a counselor comforting a distressed young woman in a bright office">
  <div class="hero-panel">
    <div class="kicker">MAPLECREST BEHAVIORAL HEALTHCARE</div>
    <div class="slogan">A STEP FORWARD IN YOUR<br><span style="font-size:24px">WELLNESS JOURNEY</span></div>
    <div class="btn-outline">TAKE A SCREENING</div>
  </div>
  <div class="dots"><span class="on"></span><span></span></div>
</section>

<!-- welcome -->
<h1 class="abs heading welcome-title">WELCOME TO</h1>
<h2 class="abs heading welcome-sub">MAPLECREST BEHAVIORAL HEALTHCARE</h2>
<p class="abs body-text" style="left:87px;top:770px;width:580px">To provide mental health services to children, adults, and the developmentally disabled population that is culturally sensitive regardless of age race, gender, orientation, religion, or creedTo work hand in hand with clients to overcome mental health challenges and improve their quality of life To partner with families and caregivers in achieving desired treatment goals for the client.</p>
<p class="abs body-text" style="left:87px;top:899px;width:580px">To provide compassionate care within an environment that fosters healing and recoveryTo bring hope and strengthen faith.We aim to offer service that patients recommend to family and friends, that other providers prefer, and is relevant in the community we serve.</p>
<div class="abs btn-green" style="left:87px;top:1005px;width:130px;height:50px;line-height:50px">READ MORE</div>

<h2 class="abs heading vision-title">VISION &amp; MISSION</h2>
<div class="photo" style="left:713px;top:726px;width:402px;height:205px;background:linear-gradient(120deg,#e9edf0,#c9d3da 55%,#eef1f3)" role="img" aria-label="Photo of a doctor shaking hands with a patient"></div>
<p class="abs body-text" style="left:713px;top:948px;width:402px">To provide compassionate care within an environment that fosters healing and recoveryTo bring hope and strengthen faith.We aim to offer ers prefer, and is relevant in the community we serve.</p>
<div class="abs link-more">READ MORE</div>

<!-- services -->
<section class="services">
  <h2 class="section-title" style="top:34px">OUR SERVICES</h2>
  <p class="section-sub" style="top:73px">To provide mental health services to children, adults, and the developmentally disabled population that is culturally sensitive</p>
  <svg class="abs" style="left:0;top:0" width="1200" height="536" viewBox="0 0 1200 536" font-family="Raleway, sans-serif" font-size="14" font-weight="600" fill="#444">
    <g stroke="#fff" stroke-width="5">
      <line x1="574" y1="282" x2="495" y2="197"/><line x1="574" y1="282" x2="682" y2="172"/>
      <line x1="574" y1="282" x2="363" y2="278"/><line x1="574" y1="282" x2="790" y2="280"/>
      <line x1="574" y1="282" x2="489" y2="311"/><line x1="574" y1="282" x2="711" y2="416"/>
    </g>
    <g fill="#c8c8c8"><circle cx="457" cy="253" r="9"/><circle cx="668" cy="316" r="11"/><circle cx="606" cy="380" r="7"/></g>
    <g fill="none" stroke="#555" stroke-width="2"><circle cx="568" cy="190" r="6"/><circle cx="727" cy="238" r="8"/><circle cx="583" cy="419" r="9"/></g>
    <g fill="#fff" stroke="#4fc3e8" stroke-width="4">
      <circle cx="495" cy="197" r="36"/><circle cx="682" cy="172" r="42"/><circle cx="363" cy="278" r="34"/>
      <circle cx="790" cy="280" r="42"/><circle cx="489" cy="311" r="32"/><circle cx="711" cy="416" r="50"/>
    </g>
    <g fill="none" stroke="#4fc3e8" stroke-width="2.5">
      <rect x="484" y="183" width="22" height="28" rx="2"/><path d="M489 198h12M495 192v12"/>
      <circle cx="682" cy="172" r="16"/><path d="M675 177q7 6 14 0"/>
      <rect x="352" y="268" width="22" height="18" rx="2"/><path d="M363 272v10M358 277h10"/>
      <rect x="773" y="272" width="34" height="16" rx="8" transform="rotate(-35 790 280)"/>
      <circle cx="486" cy="300" r="4"/><path d="M486 305v12h10l4 8M480 312a10 10 0 1 0 14 8"/>
      <path d="M693 430q18 14 36 0M711 398l6 6-6 6-6-6zM701 408l6 6-6 6-6-6zM721 408l6 6-6 6-6-6z"/>
    </g>
    <circle cx="574" cy="282" r="54" fill="#8dc63f" stroke="#fff" stroke-width="5"/>
    <text x="574" y="278" text-anchor="middle" fill="#fff" font-size="14">Psychophar</text>
    <text x="574" y="297" text-anchor="middle" fill="#fff" font-size="14">macology</text>
    <text x="385" y="176" text-anchor="middle">Diagnostic evaluation</text>
    <text x="385" y="197" text-anchor="middle">&amp; treatment</text>
    <text x="790" y="155" text-anchor="middle">Early childhood</text>
    <text x="790" y="176" text-anchor="middle">Assessments</text>
    <text x="250" y="274" text-anchor="middle">Bariatric pre-</text>
    <text x="250" y="295" text-anchor="middle">surgical consultation</text>
    <text x="904" y="270" text-anchor="middle">Substance abuse</text>
    <text x="904" y="291" text-anchor="middle">assessments</text>
    <text x="486" y="367" text-anchor="middle">Disability and work-</text>
    <text x="486" y="388" text-anchor="middle">related reports</text>
    <text x="840" y="410" text-anchor="middle">Developmental</text>
    <text x="840" y="431" text-anchor="middle">disabilities</text>
  </svg>
</section>

<!-- prospective services -->
<h2 class="abs heading prosp-title">PROSPECTIVE SERVICES</h2>
<ul class="checklist">
  <li><svg width="14" height="11" viewBox="0 0 14 11"><path d="M1 6l4 4 8-9" fill="none" stroke="#8dc63f" stroke-width="2.5"/></svg>Telepsychiatry</li>
  <li><svg width="14" height="11" viewBox="0 0 14 11"><path d="M1 6l4 4 8-9" fill="none" stroke="#8dc63f" stroke-width="2.5"/></svg>Group Therapy (Anger, Pregnancy*, Autism, Grief*, Obesity*)</li>
  <li><svg width="14" height="11" viewBox="0 0 14 11"><path d="M1 6l4 4 8-9" fill="none" stroke="#8dc63f" stroke-width="2.5"/></svg>Family Therapy</li>
  <li><svg width="14" height="11" viewBox="0 0 14 11"><path d="M1 6l4 4 8-9" fill="none" stroke="#8dc63f" stroke-width="2.5"/></svg>Back-up psychiatry* for out of towners, confidential off record</li>
  <li><svg width="14" height="11" viewBox="0 0 14 11"><path d="M1 6l4 4 8-9" fill="none" stroke="#8dc63f" stroke-width="2.5"/></svg>Parenting class</li>
  <li><svg width="14" height="11" viewBox="0 0 14 11"><path d="M1 6l4 4 8-9" fill="none" stroke="#8dc63f" stroke-width="2.5"/></svg>Medication clinics</li>
  <li><svg width="14" height="11" viewBox="0 0 14 11"><path d="M1 6l4 4 8-9" fill="none" stroke="#8dc63f" stroke-width="2.5"/></svg>TMS</li>
</ul>

<!-- faq -->
<h2 class="abs heading faq-title">FAQ'S</h2>
<div class="faq-item" style="top:1729px">How do you know if you need to see a psychiatrist, therapist, counselor
  <svg width="14" height="14" viewBox="0 0 14 14"><circle cx="7" cy="7" r="6" fill="none" stroke="#777"/><path d="M4 7h6M7 4v6" stroke="#777"/></svg></div>
<p class="abs faq-answer">A- If you're interested or curious, just go. People go to therapy for a host of reasons -- anything from getting support, to getting help for major mental illness, to working through a particular issue(s), to just getting an outsider's perspective on the issue(s)</p>
<div class="faq-item" style="top:1888px">Why is my child not doing well in school?
  <svg width="14" height="14" viewBox="0 0 14 14"><circle cx="7" cy="7" r="6" fill="none" stroke="#777"/><path d="M4 7h6M7 4v6" stroke="#777"/></svg></div>
<div class="faq-item" style="top:1944px">I feel sad, tired and I do not have energy. Is that normal?
  <svg width="14" height="14" viewBox="0 0 14 14"><circle cx="7" cy="7" r="6" fill="none" stroke="#777"/><path d="M4 7h6M7 4v6" stroke="#777"/></svg></div>

<!-- news -->
<section class="news">
  <h2 class="section-title" style="top:34px">LATEST NEWS</h2>
  <p class="section-sub" style="top:76px">To provide mental health services to children, adults, and the developmentally disabled population that is culturally sensitive</p>
  <article class="card" style="left:87px">
    <div class="pic" style="background:linear-gradient(135deg,#eef0f1,#c9cdd0)" role="img" aria-label="Photo of a stressed person holding their head"></div>
    <h3>SED UT PERSPICIATIS..</h3>
    <div class="meta"><span>&#9719; 27 MARCH 2017</span><span>&#9675; 120</span><span>&#9825; LIKE</span><span>&#8599; SHARE</span></div>
    <p>Sed ut perspiciatis unde omnis iste natus error sit volupta-tem accusantium doloremque laudantium, totam rem aper architecto beatae vitae dicta sunt explicabo.</p>
  </article>
  <article class="card" style="left:437px">
    <div class="pic" style="background:linear-gradient(135deg,#5a6f86,#c7a38c 60%,#e3d4c8)" role="img" aria-label="Photo of two people holding hands in support"></div>
    <h3>SED UT PERSPICIATIS..</h3>
    <div class="meta"><span>&#9719; 27 MARCH 2017</span><span>&#9675; 120</span><span>&#9825; LIKE</span><span>&#8599; SHARE</span></div>
    <p>Sed ut perspiciatis unde omnis iste natus error sit volupta-tem accusantium doloremque laudantium, totam rem aper architecto beatae vitae dicta sunt explicabo.</p>
  </article>
  <article class="card" style="left:788px">
    <div class="pic" style="background:linear-gradient(135deg,#f2ede6,#d8c9b6 55%,#eef0f2)" role="img" aria-label="Photo of a caregiver with an elderly woman"></div>
    <h3>SED UT PERSPICIATIS..</h3>
    <div class="meta"><span>&#9719; 27 MARCH 2017</span><span>&#9675; 120</span><span>&#9825; LIKE</span><span>&#8599; SHARE</span></div>
    <p>Sed ut perspiciatis unde omnis iste natus error sit volupta-tem accusantium doloremque laudantium, totam rem aper architecto beatae vitae dicta sunt explicabo.</p>
  </article>
</section>

<!-- footer -->
<footer class="footer">
  <div class="foot-brand">
    <span class="brand-mark"></span>
    <div class="brand-name">Maplecrest Behavioral Healthcare</div>
  </div>
  <h4 style="left:410px">CONTACT US</h4>
  <ul class="contact-list">
    <li><span>&#9742;</span>(770)-555-0142 (Phone)</li>
    <li><span>&#9113;</span>(770)-555-0143 (Fax)</li>
    <li><span>&#9993;</span><u>info@maplecrestbh.com</u></li>
    <li><span>&#9906;</span>#&nbsp;214 Lorem Ipsum dummy<br>Text Lorem</li>
  </ul>
  <h4 style="left:670px">NEWSLETTER</h4>
  <p class="news-text">Register Your email address to get information about us</p>
  <div class="email-input">Email Address</div>
  <div class="btn-green subscribe">SUBSCRIBE</div>
  <h4 style="left:950px">QUICK LINKS</h4>
  <ul class="quick">
    <li>&#187; <span>Home</span></li><li>&#187; <span>About Us</span></li><li>&#187; <span>Services</span></li>
    <li>&#187; <span>Conditions We Treat</span></li><li>&#187; <span>New Patients</span></li><li>&#187; <span>Contact Us</span></li>
  </ul>
  <div class="foot-rule"></div>
  <div class="copyright">© Copyright 2017 Maplecrest Behavioral Healthcare.All Rights Reserved</div>
  <div class="social"></div>
</footer>

</body>
</html>
```